Flyer-Design für Startup
Zielgruppe
Unser Unternehmen ist ein Startup in der Bildungslandschaft. Hinsichtlich dem Flyer besteht die Zielgruppe aus Studierenden im Alter zwischen 25 und 40 Jahren.
Aufgabenstellung
Die Texte sollten in der Vektor Datei bearbeitbare sein!
Die Frau im Feld sowie die Farben des Logos sollten im Flyer berücksichtigt werden. Zudem sollen die Inhalte auch grafisch aufgearbeitet werden. Format: Es soll ein 6-seitiger Zickzackfalz sein.
Unsere Webseite ist vorübergehend nur im Entwurfsmodus durch das Passwort 'lumacor4727' erreichbar.
Schriftart Helvetica!

```html
<!DOCTYPE html>
<html lang="de">
<head>
<meta charset="utf-8">
<title>Lumacor – Aufstiegsfortbildung Zickzackfalz</title>
<link rel="stylesheet" href="https://fonts.googleapis.com/css2?family=Playfair+Display:wght@400;700;800&family=Raleway:wght@300;400;500&display=swap">
<style>
:root{
  --navy:#1b2a4e;
  --paper:#edecec;
  --backdrop:#e2e2e2;
  --ink-grey:#7d7d80;
  --ink-dark:#1b2a4e;
  --ink-light:#d3d7e0;
  --ink-white:#eef0f4;
  --ink-muted:#a9afbf;
  --icon-grey:#c9c6c6;
  --icon-navy:#4a5675;
}
*{box-sizing:border-box;margin:0;padding:0}
html,body{width:847px;height:1200px;overflow:hidden;background:var(--backdrop)}
.canvas{position:relative;width:847px;height:1200px;overflow:hidden;font-family:"Raleway",Helvetica,Arial,sans-serif;font-weight:300;hyphens:auto;-webkit-hyphens:auto}
.panel{position:absolute;width:272px;height:577px;overflow:hidden}
.panel--light{background:var(--paper);color:var(--ink-grey)}
.panel--navy{background:var(--navy);color:var(--ink-light)}
.abs{position:absolute}
.flow{position:absolute}
.tab{position:absolute;background:var(--navy);display:flex;align-items:center;justify-content:center}
.tab-name{font-weight:500;font-size:15px;color:var(--paper);letter-spacing:.5px}
.brand-name{font-weight:500;font-size:17px;color:var(--ink-light);letter-spacing:.5px;text-align:center}
.heading{font-family:"Playfair Display",Georgia,serif;font-weight:800;font-size:16.5px;letter-spacing:1.6px;line-height:20px;hyphens:none}
.panel--light .heading{color:var(--ink-dark)}
.panel--navy .heading{color:#e6e8ee}
.vertical-title{position:absolute;writing-mode:vertical-rl;font-family:"Playfair Display",Georgia,serif;font-weight:800;font-size:42px;line-height:1;letter-spacing:.5px;hyphens:none}
.panel--light .vertical-title{color:var(--ink-dark)}
.panel--navy .vertical-title{color:var(--ink-white)}
.body{font-size:10px;line-height:12.4px;letter-spacing:.1px;text-align:justify}
.label{font-weight:500;color:var(--ink-dark)}
.panel--navy .label{color:var(--ink-white)}
.sub{font-size:10px;font-weight:500;letter-spacing:.3px;line-height:12.4px;color:var(--ink-white)}
.list{list-style:none;font-size:10px;line-height:12.4px;letter-spacing:.2px}
.list li{padding-left:8px;text-indent:-5px}
.list li::before{content:"• ";font-size:8px}
.icon{position:absolute}
.photo{position:absolute;left:0;top:0;width:272px;height:510px;background:linear-gradient(180deg,#9fb2b8 0%,#c9c4b0 38%,#c79a5c 62%,#a97438 100%)}
.photo-figure{position:absolute;left:10px;top:150px;width:250px;height:360px;background:radial-gradient(ellipse at 60% 60%,rgba(236,232,224,.75) 0%,rgba(236,232,224,.25) 45%,rgba(0,0,0,0) 70%)}
.cover-claim{font-family:"Playfair Display",Georgia,serif;font-size:18px;line-height:23px;color:var(--ink-white);text-align:center;letter-spacing:.3px;font-weight:400}
.cover-claim b{font-weight:800}
.specs{list-style:none;font-size:7.4px;line-height:10.2px;letter-spacing:0;color:var(--ink-muted)}
.specs li{padding-left:8px;text-indent:-4px;margin-top:1.5px}
.specs li::before{content:"• "}
.contact{text-align:right;font-size:11px;line-height:13.5px;letter-spacing:.2px;color:#b8bdc9;hyphens:none}
</style>
</head>
<body>
<div class="canvas">

<!-- Außenseite: Zielsetzung -->
<section class="panel panel--light" style="left:15px;top:15px">
  <div class="tab" style="left:61px;top:0;width:119px;height:82px"><span class="tab-name">Lumacor</span></div>
  <div class="flow" style="left:35px;top:124px;width:158px">
    <h2 class="heading" style="margin-left:3px">ZIELSETZUNG</h2>
    <div style="margin-top:6px">
      <svg style="float:left;margin:0 4px 0 -14px" width="62" height="66" viewBox="0 0 62 66" aria-hidden="true">
        <ellipse cx="31" cy="52" rx="29" ry="11" fill="none" stroke="var(--icon-grey)" stroke-width="2"/>
        <path d="M31 2a20 20 0 0 0-20 20c0 15 20 34 20 34s20-19 20-34A20 20 0 0 0 31 2z" fill="var(--icon-grey)"/>
        <circle cx="31" cy="22" r="9" fill="var(--paper)"/>
      </svg>
      <p class="body">Dieser Kurs bereitet Sie auf die Prüfung zum/r geprüften Wirtschaftsfachwirt/in (IHK) vor.</p>
    </div>
    <p class="body" style="clear:both;padding-top:6px">Die Anmeldung zur Prüfung bei der für Sie örtlich zuständigen Industrie- und Handelskammer erfolgt durch den Teilnehmer und die Prüfung ist innerhalb des Maßnahmenzeitraums abzulegen.</p>
    <h2 class="heading" style="margin-top:20px">VOLLZEIT</h2>
    <div class="body" style="margin-top:4px;text-align:left">
      <svg style="float:right;margin:6px -46px 0 2px" width="60" height="66" viewBox="0 0 60 66" aria-hidden="true">
        <g fill="none" stroke="var(--icon-grey)" stroke-width="3">
          <rect x="6" y="10" width="44" height="40" rx="5" transform="rotate(14 28 30)"/>
          <line x1="16" y1="4" x2="14" y2="13"/><line x1="38" y1="8" x2="36" y2="17"/>
          <circle cx="44" cy="48" r="13" fill="var(--paper)"/>
          <path d="M44 41v8l5 3"/>
        </g>
      </svg>
      <p><span class="label">Kursformat :</span> Virtuelles Klassenzimmer mittels Konvia (ortsunabhängig)</p>
      <p style="margin-top:5px"><span class="label">Kursdauer:</span> 24 Wochen</p>
      <p style="margin-top:5px"><span class="label">Unterrichtszeiten:</span> Montag bis Freitag von 8:00 – 16:00 Uhr</p>
      <p style="margin-top:5px"><span class="label">Kursstart:</span> Maximale Flexibilität! Aufgrund des rollierenden Systems ist ein Kursstart zu Beginn der jeweiligen Module jederzeit modulunabhängig möglich.</p>
    </div>
  </div>
  <h1 class="vertical-title" style="left:214px;top:93px">Zielsetzung</h1>
  <div class="tab" style="left:61px;top:555px;width:119px;height:22px"></div>
</section>

<!-- Außenseite: Kosten / Inhalte -->
<section class="panel panel--navy" style="left:288px;top:15px">
  <div class="flow" style="left:22px;top:17px;width:217px;height:550px;display:flex;flex-direction:column">
    <div>
      <svg style="float:left;margin:4px 6px 0 -8px" width="60" height="80" viewBox="0 0 60 74" aria-hidden="true">
        <g fill="none" stroke="var(--icon-navy)" stroke-width="2.5" transform="rotate(12 30 37)">
          <rect x="8" y="4" width="44" height="66" rx="6"/>
          <rect x="15" y="11" width="30" height="12" rx="2"/>
          <rect x="15" y="29" width="8" height="7"/><rect x="26" y="29" width="8" height="7"/><rect x="37" y="29" width="8" height="7"/>
          <rect x="15" y="40" width="8" height="7"/><rect x="26" y="40" width="8" height="7"/><rect x="37" y="40" width="8" height="7"/>
          <rect x="15" y="51" width="8" height="7"/><rect x="26" y="51" width="8" height="7"/><rect x="37" y="51" width="8" height="7"/>
        </g>
      </svg>
      <h2 class="heading">KOSTEN</h2>
      <p class="body" style="margin-top:3px;font-size:9.6px;line-height:12.3px;letter-spacing:0">Die Maßnahme ist nach AZAV durch die ZertPro als fachkundige Stelle zugelassen und erfüllt damit die Voraussetzung der Förderung über einen Bildungsgutschein durch die Agentur für Arbeit (SGB III) bzw. JobCenter (SGB II), durch Rentenversicherungsträger oder nach dem Soldatenversorgungsgesetz von bis 100 % der Kosten. Die lokalen Agenturen für Arbeit bzw. JobCenter, die Rentenversicherungsträger oder die Berufsförderungsdienste erteilen hierzu nähere Auskünfte.</p>
    </div>
    <h2 class="heading" style="margin-top:10px">INHALTE</h2>
    <p class="sub" style="margin-top:4px">Wirtschaftsbezogene Qualifikationen</p>
    <ul class="list" style="margin:3px 0 5px 12px">
      <li>Volks- und Betriebswirtschaft</li><li>Rechnungswesen</li><li>Recht und Steuern</li><li>Unternehmensführung</li>
    </ul>
    <p class="sub">Handlungsspezifische Qualifikationen</p>
    <ul class="list" style="margin:3px 0 0 12px">
      <li>Betriebliches Management</li><li>Investition, Finanzierung, betriebliches Rechnungswesen und Controlling</li><li>Logistik</li><li>Marketing und Vertrieb</li><li>Führung und Zusammenarbeit</li>
    </ul>
    <div style="position:relative;margin-top:12px">
      <h2 class="heading">IHR PERSÖNLICHER<br>VORTEIL</h2>
      <svg class="icon" style="left:170px;top:4px" width="64" height="68" viewBox="0 0 64 68" aria-hidden="true">
        <g fill="none" stroke="var(--icon-navy)" stroke-width="2.5" stroke-linejoin="round">
          <path d="M4 44 12 6l20 8 24-6-6 40-22 4z"/><path d="M32 14 28 52"/>
          <path d="M40 40v-12a4 4 0 0 1 8 0v14l8 2v10c0 6-4 10-10 10h-4c-4 0-8-4-10-8l-4-8 4-2 6 6"/>
        </g>
      </svg>
    </div>
    <ul class="list" style="margin:4px 0 0 12px;position:relative">
      <li>Zeugnis des Trägers und/oder</li><li>Teilnahmebescheinigung</li><li>Bundesweit anerkannter IHK-Abschluss</li><li>Querschnittsübergreifendes Fachwissen</li><li>Qualifizierung zur Übernahme einer höheren Position</li>
    </ul>
    <p style="margin-top:auto;font-size:10px;line-height:12.4px;font-weight:400;letter-spacing:.1px;color:var(--ink-white);hyphens:none">Weiterqualifizierung zum Master Professional of Business Management (CCI) ist nach Erhalt des Abschlusses möglich</p>
  </div>
</section>

<!-- Titelseite -->
<section class="panel panel--navy" style="left:560px;top:15px">
  <div class="photo" role="img" aria-label="Foto: Frau im weißen Kleid läuft mit wehendem Haar durch ein goldenes Getreidefeld unter hellem Himmel">
    <div class="photo-figure"></div>
  </div>
  <div class="tab" style="left:72px;top:0;width:119px;height:82px"></div>
  <p class="brand-name abs" style="left:0;top:96px;width:272px;font-size:25px;color:var(--ink-dark)">Lumacor</p>
  <p class="abs" style="left:0;top:128px;width:272px;text-align:center;font-family:'Playfair Display',Georgia,serif;font-weight:800;font-size:23px;letter-spacing:.4px;color:var(--ink-dark)">Aufstiegsfortbildung</p>
  <p class="cover-claim abs" style="left:0;top:521px;width:272px">Werde jetzt <b>Geprüfte/r</b><br><b>Wirtschaftsfachwirt/in</b> (IHK)</p>
</section>

<!-- Innenseite: Aufstiegsfortbildung -->
<section class="panel panel--navy" style="left:15px;top:610px">
  <p class="brand-name abs" style="left:30px;top:40px;width:160px">Lumacor</p>
  <div class="flow" style="left:35px;top:120px;width:155px">
    <p class="body">Eine <span class="label">Aufstiegsfortbildung zum/zur Wirtschaftsfachwirt/-in</span> vermittelt generalistisches Fachwissen im Bereich Handel, Industrie sowie Dienstleistungen und zählt insofern als Allrounder zu den populärsten Aufstiegsfortbildungen im kaufmännischen Bereich. Wirtschaftsfachwirte übernehmen in der Regel Führungsaufgaben und können betriebswirtschaftliche Zusammenhänge in ihrem Gesamtzusammenhang erkennen und beurteilen.</p>
    <p class="body" style="margin-top:12px">Der Abschluss zum/zur Wirtschaftsfachwirt/-in ist eine echte Alternative zum klassischen Bachelorstudium an einer Hochschule. Der wesentliche Unterschied liegt in der praxisnahen Auslegung der Theorieinhalte.</p>
    <p style="margin-top:10px;font-size:11.5px;line-height:13.6px;letter-spacing:.2px;text-align:justify;color:var(--ink-white);font-weight:400">Mit der Zuordnung auf DQR-Stufe 6 befindet sich der Abschluss auf derselben</p>
    <div style="display:flex;align-items:flex-start;gap:6px;margin-top:2px">
      <p style="width:90px;font-size:11.5px;line-height:13.6px;letter-spacing:.2px;color:var(--ink-white);font-weight:400">Stufe wie die Bachelor-Abschlüsse der Hochschulen.</p>
      <svg style="margin-top:2px" width="62" height="78" viewBox="0 0 64 80" aria-hidden="true">
        <g transform="rotate(10 32 40)">
          <rect x="6" y="4" width="50" height="62" rx="5" fill="var(--icon-navy)"/>
          <g stroke="var(--navy)" stroke-width="3"><line x1="14" y1="16" x2="46" y2="16"/><line x1="14" y1="25" x2="46" y2="25"/><line x1="14" y1="34" x2="40" y2="34"/><line x1="14" y1="43" x2="30" y2="43"/></g>
          <circle cx="42" cy="56" r="9" fill="var(--icon-navy)" stroke="var(--navy)" stroke-width="2.5"/>
          <path d="M37 64l-2 12 6-4 2 6 4-12" fill="var(--icon-navy)"/>
        </g>
      </svg>
    </div>
  </div>
  <h1 class="vertical-title" style="left:214px;top:88px">Aufstiegsfortbildung</h1>
</section>

<!-- Innenseite: Fachliche Voraussetzungen -->
<section class="panel panel--light" style="left:288px;top:610px">
  <div class="tab" style="left:72px;top:0;width:118px;height:87px"><span class="tab-name">Lumacor</span></div>
  <div class="flow" style="left:22px;top:96px;width:226px;font-size:9.8px;line-height:12.2px;letter-spacing:0">
    <h2 class="heading">FACHLICHE<br>VORAUSSETZUNGEN</h2>
    <p style="margin-top:5px">Für die Teilprüfung</p>
    <p class="label" style="margin-top:3px">„Wirtschaftsbezogene Qualifikationen“</p>
    <ul class="list" style="margin:3px 0 0 14px;font-size:9.8px;line-height:12.2px;letter-spacing:0">
      <li style="margin-bottom:5px">werden Sie zugelassen, wenn Sie eine erfolgreich bestandene Abschlussprüfung in einem anerkannten mindestens dreijährigen kaufmännischen oder verwaltenden Ausbildungsberuf haben, oder</li>
      <li style="margin-bottom:5px">eine erfolgreich bestandene Abschlussprüfung in einem sonstigen anerkannten mindestens dreijährigen Ausbildungsberuf und danach mindestens ein Jahr Berufspraxis vorweisen können, oder</li>
      <li style="margin-bottom:5px">eine erfolgreich bestandene Abschlussprüfung in einem anderen anerkannten Ausbildungsberuf und danach mindestens zwei Jahre Berufspraxis gesammelt haben, oder</li>
      <li>mindestens drei Jahre Berufspraxis vorweisen können.</li>
    </ul>
    <p style="margin-top:5px">Für die Teilprüfung</p>
    <p class="label" style="margin-top:3px">„Handlungsspezifische Qualifikationen“</p>
    <p style="margin:3px 0 0 15px">werden Sie zugelassen, wenn die abgelegte Teilprüfung „Wirtschaftsbezogene Qualifikationen“, nicht länger als fünf Jahre zurückliegt und Sie mindestens ein weiteres Jahr Berufspraxis zu den Zulassungsvoraussetzungen unter der Teilprüfung „Wirtschaftsbezogene Qualifikationen“ nachweisen können.</p>
    <p style="margin-top:2px;font-size:7px;line-height:9px;letter-spacing:0">Den Antrag auf Prüfung der Zulassungsvoraussetzungen erhalten Sie bei Ihrer zuständigen Industrie- und Handelskammer.</p>
  </div>
  <div class="tab" style="left:76px;top:557px;width:118px;height:20px"></div>
</section>

<!-- Innenseite: Technische Voraussetzungen / Kursanmeldung -->
<section class="panel panel--navy" style="left:560px;top:610px">
  <p class="brand-name abs" style="left:95px;top:40px;width:160px">Lumacor</p>
  <h1 class="vertical-title" style="left:14px;top:92px">Voraussetzungen</h1>
  <div class="flow" style="left:66px;top:96px;width:194px">
    <h2 class="heading">TECHNISCHE<br>VORAUSSETZUNGEN</h2>
    <p class="body" style="margin-top:4px;color:var(--ink-muted);font-size:9.8px;line-height:12px;letter-spacing:0">Für die Teilnahme an der Fortbildung benötigen Sie einen PC, der die folgenden Hardwareanforderungen für Fenestra-Systeme erfüllt:</p>
    <ul class="specs" style="margin:2px 0 0 8px">
      <li>Computer und Prozessor: Mindestens 1,6 GHz (oder höher), 2-Core-Prozessor</li>
      <li>Arbeitsspeicher: 4,0 GB RAM</li>
      <li>Festplatte: 3,0 GB verfügbarer Speicherplatz</li>
      <li>Anzeige: Bildschirmauflösung 1024x768 Pixel</li>
      <li>Grafikkarte: Grafikhardwarebeschleunigung erfordert GrafiX 9 oder höher, mit GTM 2.0 oder höher für Fenestra 10</li>
    </ul>
    <div style="display:flex;justify-content:space-between;align-items:flex-start;margin-left:8px">
      <ul class="specs" style="width:96px">
        <li>Betriebssystem:<br>Fenestra 8</li>
        <li>Video: USB 2.0-Videokamera (oder interne</li>
      </ul>
      <svg style="margin-top:-4px" width="80" height="58" viewBox="0 0 84 66" aria-hidden="true">
        <rect x="4" y="12" width="58" height="44" rx="2" fill="none" stroke="var(--icon-navy)" stroke-width="2.5" transform="rotate(-4 33 34)"/>
        <circle cx="28" cy="30" r="7" fill="var(--icon-navy)"/>
        <path d="M16 52c0-10 6-14 12-14s12 4 12 14z" fill="var(--icon-navy)"/>
        <path d="M56 2h18a8 8 0 0 1 8 8v8a8 8 0 0 1-8 8h-10l-8 6 2-6a8 8 0 0 1-10-8v-8a8 8 0 0 1 8-8z" fill="var(--icon-navy)"/>
        <g fill="var(--navy)"><circle cx="62" cy="14" r="2"/><circle cx="69" cy="14" r="2"/><circle cx="76" cy="14" r="2"/></g>
      </svg>
    </div>
    <h2 class="heading" style="margin-top:10px">KURSANMELDUNG</h2>
    <div style="margin-top:4px;font-size:10.4px;line-height:13px;letter-spacing:-.25px;color:var(--ink-muted);hyphens:none">
      <p>Die Kursanmeldung erfolgt nach einem persönlichen Beratungsgespräch.</p>
      <p style="margin-top:5px">Nehmen Sie hierzu gerne Kontakt mit uns auf. Wir freuen uns schon sehr!</p>
    </div>
    <div style="position:relative;margin-top:8px;height:110px">
      <svg class="icon" style="left:-22px;top:8px" width="78" height="78" viewBox="0 0 80 80" aria-hidden="true">
        <g fill="none" stroke="var(--icon-navy)" stroke-width="2.5" stroke-linejoin="round">
          <path d="M6 16 42 6l14 8 10 46-48 14z" transform="rotate(-2 40 40)"/>
          <line x1="20" y1="30" x2="44" y2="24"/><line x1="22" y1="38" x2="46" y2="32"/><line x1="24" y1="46" x2="40" y2="42"/>
          <path d="M28 62c4-6 8 2 12-4"/>
          <path d="M72 6l6 4-22 34-8 4 2-8z"/>
        </g>
      </svg>
      <div class="contact abs" style="right:20px;top:0;width:130px">
        <p>Lumacor GmbH</p><p>Lindenallee 5-9</p><p>32099 Birkental</p>
        <p style="margin-top:10px">+49-(0)5231-4402916</p><p>info@lumacor.de</p><p>www.lumacor.de</p>
      </div>
    </div>
  </div>
</section>

</div>
</body>
</html>
```